Company document Header needed

Using our current logo, I need a Designer to create a header for use on our company documents. This header will include our business address, phone, fax, website address

Project Deadline Extended
Reason: Dear designers, I am so pleased with the many different options that have been presented, that I wish to purchase several of them from a few different designers. I will get with the pixel hive folks and figure out what is the best way to do this. In the meantime, I am extending the deadline to allow for a few edits such as our phone number and such. thanks to you all for your excellent work. RK

Designers,

Please take a look and edit any of your submissions that have incorrect info on them:  the correct info is below:

Business name is: Tarvel Crest, Inc.

website address is:  www.tarvelcrest-example.com

Office #:  (855) TarvelC  

Fax#:  (858) 512-6194  (generally I do not intend to need this on any materials unless it balances a look)

email:  info@tarvelcrest-example.com

Address:  472 Marlow St. suite 2260  San Diego, CA  92187

Thanks!

```html
<!DOCTYPE html>
<html lang="en">
<head>
<meta charset="utf-8">
<title>Tarvel Crest Letterhead</title>
<link href="https://fonts.googleapis.com/css2?family=PT+Sans+Narrow:wght@400;700&display=swap" rel="stylesheet">
<style>
  :root {
    --backdrop: #e6e6e6;
    --paper: #ffffff;
    --brand-blue: #0e5a86;
    --brand-blue-deep: #0a4a70;
    --ink-grey: #5a5a5a;
    --stripe: #e4f3fb;
  }
  html, body {
    margin: 0;
    padding: 0;
    width: 1200px;
    height: 907px;
    overflow: hidden;
    background: var(--backdrop);
  }
  .canvas {
    position: relative;
    width: 1200px;
    height: 907px;
  }
  .letterhead {
    position: absolute;
    left: 307px;
    top: 39px;
    width: 582px;
    height: 820px;
    background: var(--paper);
    box-shadow: 0 2px 8px rgba(0,0,0,0.18);
    overflow: hidden;
  }
  .header-band {
    position: absolute;
    left: 71px;
    top: 104px;
    width: 511px;
    height: 62px;
    background: linear-gradient(180deg, rgba(228,243,251,0.9) 0%, var(--stripe) 50%, rgba(228,243,251,0.7) 100%);
  }
  .brand-block {
    position: absolute;
    left: 243px;
    top: 0;
    width: 98px;
    height: 98px;
    background: linear-gradient(160deg, var(--brand-blue) 0%, var(--brand-blue-deep) 100%);
    display: flex;
    align-items: flex-end;
    justify-content: center;
    padding-bottom: 10px;
    box-sizing: border-box;
  }
  .brand-name {
    font-family: "PT Sans Narrow", sans-serif;
    font-weight: 700;
    font-size: 15px;
    letter-spacing: 0.2px;
    color: #ffffff;
    text-align: center;
    line-height: 1;
    white-space: nowrap;
  }
  .contact {
    position: absolute;
    left: 355px;
    top: 15px;
    font-family: "PT Sans Narrow", sans-serif;
    font-size: 8.4px;
    line-height: 10px;
    color: var(--ink-grey);
    white-space: nowrap;
  }
  .contact p { margin: 0; }
  .contact .company {
    font-weight: 700;
    color: var(--brand-blue);
  }
  .contact .website {
    margin-top: 6px;
    font-weight: 700;
    color: var(--brand-blue);
  }
</style>
</head>
<body>
<div class="canvas">
  <div class="letterhead">
    <div class="header-band" role="img" aria-label="Soft light blue decorative band across the header"></div>
    <div class="brand-block">
      <span class="brand-name">TARVEL CREST</span>
    </div>
    <div class="contact">
      <p class="company">Tarvel Crest, Inc.</p>
      <p>472 Marlow St. suite 2260 San Diego,</p>
      <p>CA&nbsp; 92187</p>
      <p>Office: (855) TarvelC</p>
      <p>Fax: (858) 512-6194</p>
      <p>email: info@tarvelcrest-example.com</p>
      <p class="website">www.tarvelcrest-example.com</p>
    </div>
  </div>
</div>
</body>
</html>
```